Onboarding Carousel UI/UX design

We need a great UI/UX design for our onboarding carousel as attached in the PDF document. The chosen designers will be given our brand book with colors and styles to be used. The images must be focused on the content of each slide and be professional unique style (Do not use the childish cartoons we have used for placeholders)

Industry/Entity Type

Mortgage Brokerage

Number of Pages Required

5+ page

Font styles to use
Other font styles liked:
• Roboto

Requirements
Must have
• Great UI / UX design
Very relevant content of the images to match the slide
Nice to have
• Brand book

https://pv.lumorak.com/view/ed991dda-3474-4c3e-9747-882e21ba3df5-b8ca/?fullscreen

Image styles we like. Would need to be customized and made unique for us.

https://pinvarlo.com/shots/6300615-Torvane-Quillet-Illustration-Collaboration
https://meltridgestudio.co.za/software-client-style-frames
Should not have
• Do not use the childish images we have used as placeholders

```html
<!DOCTYPE html>
<html lang="en">
<head>
<meta charset="utf-8">
<title>Onboarding Carousel – Halvern Brokers</title>
<link href="https://fonts.googleapis.com/css2?family=Roboto:wght@300;400;500;700&display=swap" rel="stylesheet">
<style>
  :root {
    --canvas: #e8e8e8;
    --screen: #ffffff;
    --navy: #0f2d5c;
    --brand-blue: #0565c0;
    --accent-pink: #e2147b;
    --logon-olive: #7b8a00;
    --text-dark: #1e1e1e;
    --text-muted: #555a60;
    --dot-idle: #9a9a9a;
    --dot-first: #1e1e1e;
  }
  * { box-sizing: border-box; margin: 0; padding: 0; }
  html, body { width: 779px; height: 1200px; overflow: hidden; }
  body {
    background: var(--canvas);
    font-family: "Roboto", Arial, sans-serif;
    position: relative;
  }
  .screen {
    position: absolute;
    width: 212px;
    height: 460px;
    background: var(--screen);
    border-radius: 22px;
    overflow: hidden;
    box-shadow: 0 6px 18px rgba(0,0,0,.12);
  }
  .screen--welcome  { left: 105px; top: 94px; }
  .screen--account  { left: 450px; top: 94px; }
  .screen--mobile   { left: 105px; top: 634px; }
  .screen--identity { left: 450px; top: 634px; }

  .status-bar {
    position: absolute; top: 5px; left: 14px; right: 12px; height: 12px;
    display: flex; justify-content: space-between; align-items: center;
    font-size: 8px; font-weight: 500; color: var(--text-dark);
  }
  .status-icons { display: flex; gap: 3px; align-items: center; }

  .illustration { position: absolute; border-radius: 40% 50% 45% 40%; }
  .screen--welcome .illustration {
    left: 20px; top: 36px; width: 179px; height: 112px;
    background: radial-gradient(ellipse at 50% 50%, #c9d6f2 0%, #dfe6f7 60%, #f4f6fc 100%);
  }
  .screen--account .illustration {
    left: 50px; top: 38px; width: 115px; height: 115px; border-radius: 18px;
    background: linear-gradient(160deg, #e3ecfb 0%, #f6e3d6 60%, #eef4e6 100%);
  }
  .screen--mobile .illustration {
    left: 24px; top: 53px; width: 164px; height: 92px; border-radius: 40% 45% 20% 20%;
    background: linear-gradient(120deg, #d6e0f8 0%, #c4d3f5 55%, #f6d79a 100%);
  }
  .screen--identity .illustration {
    left: 38px; top: 33px; width: 135px; height: 124px; border-radius: 16px;
    background: linear-gradient(180deg, #dbe7f8 0%, #b9cff0 100%);
  }

  .eyebrow, .title, .lead, .note {
    position: absolute; left: 0; right: 0; text-align: center;
  }
  .eyebrow { font-size: 8.6px; font-weight: 500; color: var(--brand-blue); }
  .title { font-size: 13px; line-height: 17px; font-weight: 500; color: var(--navy); }
  .lead { font-size: 8.9px; line-height: 15.5px; color: var(--text-dark); }
  .note { font-size: 7.3px; line-height: 13px; font-weight: 300; color: var(--text-muted); }

  .pager {
    position: absolute; left: 0; right: 0;
    display: flex; justify-content: center; gap: 3px;
  }
  .pager span {
    width: 7px; height: 7px; border-radius: 50%;
    border: 1px solid var(--dot-idle); background: transparent;
  }
  .pager span.is-active { background: var(--navy); border-color: var(--navy); }
  .screen--welcome .pager span.is-active { background: var(--dot-first); border-color: var(--dot-first); }

  .btn-next {
    position: absolute; left: 143px; width: 57px; height: 24px;
    background: var(--accent-pink); color: #fff; border-radius: 2px;
    font-size: 9px; font-weight: 700; letter-spacing: .2px;
    display: flex; align-items: center; justify-content: center;
  }
  .logon-prompt {
    position: absolute; left: 15px; top: 362px;
    font-size: 8.3px; line-height: 13px; color: var(--text-dark);
  }
  .logon-prompt strong { color: var(--logon-olive); font-weight: 500; }

  .nav-bar {
    position: absolute; left: 0; right: 0; bottom: 0; height: 40px;
    background: var(--brand-blue);
    display: flex; justify-content: space-between; align-items: center;
    padding: 0 15px 0 16px;
  }
</style>
</head>
<body>

<!-- Slide 1: welcome -->
<section class="screen screen--welcome">
  <div class="status-bar"><span>9:41</span>
    <span class="status-icons">
      <svg width="10" height="6" viewBox="0 0 10 6"><rect x="0" y="4" width="2" height="2" fill="#1e1e1e"/><rect x="3" y="3" width="2" height="3" fill="#1e1e1e"/><rect x="6" y="1.5" width="2" height="4.5" fill="#1e1e1e"/><rect x="8.5" y="0" width="1.5" height="6" fill="#1e1e1e"/></svg>
      <svg width="9" height="7" viewBox="0 0 9 7"><path d="M0.5 2.5a5.5 5.5 0 0 1 8 0M2 4a3.5 3.5 0 0 1 5 0" stroke="#1e1e1e" stroke-width="1.1" fill="none"/><circle cx="4.5" cy="5.8" r=".9" fill="#1e1e1e"/></svg>
      <svg width="12" height="6" viewBox="0 0 12 6"><rect x="0" y="0.5" width="11" height="5" rx="1" fill="#1e1e1e"/></svg>
    </span>
  </div>
  <div class="illustration" role="img" aria-label="Illustration of brokers working at desks around a world map"></div>
  <p class="eyebrow" style="top:168px">Welcome to</p>
  <h1 class="title" style="top:183px">Halvern Brokers<br>Apply Online</h1>
  <p class="lead" style="top:233px">You can apply online for your next mortgage<br>credit in about 20 minutes.</p>
  <p class="note" style="top:276px">It's easy, and we will guide you all the way.<br>See the five simple steps that you have to take!</p>
  <div class="pager" style="top:326px"><span class="is-active"></span><span></span><span></span><span></span><span></span><span></span><span></span></div>
  <p class="logon-prompt">Already have an account?<br><strong>Logon</strong></p>
  <div class="btn-next" style="top:364px">NEXT</div>
  <nav class="nav-bar">
    <svg width="12" height="12" viewBox="0 0 12 12"><path d="M1.5 1v10M6 1v10M10.5 1v10" stroke="#fff" stroke-width="1.8"/></svg>
    <svg width="11" height="11" viewBox="0 0 11 11"><rect x="1" y="1" width="9" height="9" rx="1.5" stroke="#fff" stroke-width="1.2" fill="none"/></svg>
    <svg width="8" height="12" viewBox="0 0 8 12"><path d="M6.5 1 1.5 6l5 5" stroke="#fff" stroke-width="1.5" fill="none"/></svg>
  </nav>
</section>

<!-- Slide 2: create account -->
<section class="screen screen--account">
  <div class="status-bar"><span>9:41</span>
    <span class="status-icons">
      <svg width="10" height="6" viewBox="0 0 10 6"><rect x="0" y="4" width="2" height="2" fill="#1e1e1e"/><rect x="3" y="3" width="2" height="3" fill="#1e1e1e"/><rect x="6" y="1.5" width="2" height="4.5" fill="#1e1e1e"/><rect x="8.5" y="0" width="1.5" height="6" fill="#1e1e1e"/></svg>
      <svg width="9" height="7" viewBox="0 0 9 7"><path d="M0.5 2.5a5.5 5.5 0 0 1 8 0M2 4a3.5 3.5 0 0 1 5 0" stroke="#1e1e1e" stroke-width="1.1" fill="none"/><circle cx="4.5" cy="5.8" r=".9" fill="#1e1e1e"/></svg>
      <svg width="12" height="6" viewBox="0 0 12 6"><rect x="0" y="0.5" width="11" height="5" rx="1" fill="#1e1e1e"/></svg>
    </span>
  </div>
  <div class="illustration" role="img" aria-label="Illustration of a person on a laptop connected to colleagues via video chat"></div>
  <h2 class="title" style="top:178px">#1 Create your<br>personal account</h2>
  <p class="lead" style="top:233px">You will need a valid email<br>address to create your account</p>
  <p class="note" style="top:276px">We will send you a confirmation email, make sure<br>you click the link to verify your email address.</p>
  <div class="pager" style="top:326px"><span></span><span class="is-active"></span><span></span><span></span><span></span><span></span><span></span></div>
  <div class="btn-next" style="top:364px">NEXT</div>
  <nav class="nav-bar">
    <svg width="12" height="12" viewBox="0 0 12 12"><path d="M1.5 1v10M6 1v10M10.5 1v10" stroke="#fff" stroke-width="1.8"/></svg>
    <svg width="11" height="11" viewBox="0 0 11 11"><rect x="1" y="1" width="9" height="9" rx="1.5" stroke="#fff" stroke-width="1.2" fill="none"/></svg>
    <svg width="8" height="12" viewBox="0 0 8 12"><path d="M6.5 1 1.5 6l5 5" stroke="#fff" stroke-width="1.5" fill="none"/></svg>
  </nav>
</section>

<!-- Slide 3: secure with mobile -->
<section class="screen screen--mobile">
  <div class="status-bar"><span>9:41</span>
    <span class="status-icons">
      <svg width="10" height="6" viewBox="0 0 10 6"><rect x="0" y="4" width="2" height="2" fill="#1e1e1e"/><rect x="3" y="3" width="2" height="3" fill="#1e1e1e"/><rect x="6" y="1.5" width="2" height="4.5" fill="#1e1e1e"/><rect x="8.5" y="0" width="1.5" height="6" fill="#1e1e1e"/></svg>
      <svg width="9" height="7" viewBox="0 0 9 7"><path d="M0.5 2.5a5.5 5.5 0 0 1 8 0M2 4a3.5 3.5 0 0 1 5 0" stroke="#1e1e1e" stroke-width="1.1" fill="none"/><circle cx="4.5" cy="5.8" r=".9" fill="#1e1e1e"/></svg>
      <svg width="12" height="6" viewBox="0 0 12 6"><rect x="0" y="0.5" width="11" height="5" rx="1" fill="#1e1e1e"/></svg>
    </span>
  </div>
  <div class="illustration" role="img" aria-label="Illustration of people using digital screens and a laptop for secure access"></div>
  <h2 class="title" style="top:173px">#2 Secure your account<br>with your mobile phone</h2>
  <p class="lead" style="top:228px">You will need a valid mobile phone number to<br>enable two factor authentication.</p>
  <p class="note" style="top:271px">We will send you an SMS containing<br>a security code to verify your mobile number.</p>
  <div class="pager" style="top:321px"><span></span><span></span><span class="is-active"></span><span></span><span></span><span></span><span></span></div>
  <div class="btn-next" style="top:366px">NEXT</div>
  <nav class="nav-bar">
    <svg width="12" height="12" viewBox="0 0 12 12"><path d="M1.5 1v10M6 1v10M10.5 1v10" stroke="#fff" stroke-width="1.8"/></svg>
    <svg width="11" height="11" viewBox="0 0 11 11"><rect x="1" y="1" width="9" height="9" rx="1.5" stroke="#fff" stroke-width="1.2" fill="none"/></svg>
    <svg width="8" height="12" viewBox="0 0 8 12"><path d="M6.5 1 1.5 6l5 5" stroke="#fff" stroke-width="1.5" fill="none"/></svg>
  </nav>
</section>

<!-- Slide 4: verify identity -->
<section class="screen screen--identity">
  <div class="status-bar"><span>9:41</span>
    <span class="status-icons">
      <svg width="10" height="6" viewBox="0 0 10 6"><rect x="0" y="4" width="2" height="2" fill="#1e1e1e"/><rect x="3" y="3" width="2" height="3" fill="#1e1e1e"/><rect x="6" y="1.5" width="2" height="4.5" fill="#1e1e1e"/><rect x="8.5" y="0" width="1.5" height="6" fill="#1e1e1e"/></svg>
      <svg width="9" height="7" viewBox="0 0 9 7"><path d="M0.5 2.5a5.5 5.5 0 0 1 8 0M2 4a3.5 3.5 0 0 1 5 0" stroke="#1e1e1e" stroke-width="1.1" fill="none"/><circle cx="4.5" cy="5.8" r=".9" fill="#1e1e1e"/></svg>
      <svg width="12" height="6" viewBox="0 0 12 6"><rect x="0" y="0.5" width="11" height="5" rx="1" fill="#1e1e1e"/></svg>
    </span>
  </div>
  <div class="illustration" role="img" aria-label="Blue line illustration of a team assembling puzzle pieces around a desk"></div>
  <h2 class="title" style="top:183px">#3 Verify your identity online</h2>
  <p class="lead" style="top:218px">You will need to have a valid Romanian ID<br>card or residence permit</p>
  <p class="note" style="top:260px">From your smart phone, you will take a photo of<br>your card and make a selfie video.</p>
  <div class="pager" style="top:310px"><span></span><span></span><span></span><span class="is-active"></span><span></span><span></span><span></span></div>
  <div class="btn-next" style="top:348px">NEXT</div>
  <nav class="nav-bar">
    <svg width="12" height="12" viewBox="0 0 12 12"><path d="M1.5 1v10M6 1v10M10.5 1v10" stroke="#fff" stroke-width="1.8"/></svg>
    <svg width="11" height="11" viewBox="0 0 11 11"><rect x="1" y="1" width="9" height="9" rx="1.5" stroke="#fff" stroke-width="1.2" fill="none"/></svg>
    <svg width="8" height="12" viewBox="0 0 8 12"><path d="M6.5 1 1.5 6l5 5" stroke="#fff" stroke-width="1.5" fill="none"/></svg>
  </nav>
</section>

</body>
</html>
```